Law Firm in Texas in need of new letterhead

Law Firm in Fort Worth, TX, USA named "Pell & Varnum, Attorneys-At-Law, LLP." This is a general practice law firm that mostly does Family Law and Criminal Defense work.

We are looking for a new letterhead that has a "classical" appeal, with modern elements.

Any color combination is fine, but please note that we do fax many documents, so the design must be clearly legible in Black and White.

We would like our letterhead to project a sense of professionalism, integrity, and ability.

Target Market(s)

Letterhead will be for correspondence generally with other attorneys and clients.

Industry/Entity Type

Law Firm

Logo Text

Pell & Varnum, Attorneys-At-Law, LLP.

Logo styles of interest
Pictorial/Combination Logo
Wordmark Logo
Lettermark Logo
Requirements
Nice to have
• Although not necessary, a "Texas Star" that is incorporated into the design would be a nice touch.
Should not have
• Colors that do not convert to B&W easily

```html
<!DOCTYPE html>
<html lang="en">
<head>
<meta charset="utf-8">
<title>Pell &amp; Varnum — Letterhead</title>
<link rel="stylesheet" href="https://fonts.googleapis.com/css2?family=Questrial&display=swap">
<style>
  :root {
    --backdrop: #e3e4e6;
    --paper: #ffffff;
    --brand-blue: #2d5c8f;
    --ink: #4a4a4a;
    --ink-soft: #7a7a7a;
    --rule: #8a8a8a;
    --watermark: #f1f2f4;
    --watermark-edge: #eaebee;
  }
  * { box-sizing: border-box; margin: 0; padding: 0; }
  html, body { width: 1200px; height: 1000px; overflow: hidden; }
  body {
    background: var(--backdrop);
    font-family: "Questrial", "Century Gothic", sans-serif;
    color: var(--ink);
  }
  .letterhead {
    position: absolute;
    left: 250px; top: 40px;
    width: 700px; height: 920px;
    background: var(--paper);
    box-shadow: 0 6px 24px rgba(0,0,0,0.12);
  }
  .masthead {
    position: absolute; top: 60px; left: 0; right: 0;
    text-align: center;
    font-family: "Questrial", sans-serif;
    font-size: 22px; letter-spacing: 0.5px;
    color: var(--brand-blue);
  }
  .star-watermark {
    position: absolute; left: 190px; top: 190px; width: 320px; height: 320px;
    border-radius: 50%;
    background: radial-gradient(circle at 50% 50%, var(--watermark) 0%, var(--watermark-edge) 55%, var(--paper) 72%);
    opacity: 0.7;
  }
  .letter-body {
    position: absolute; left: 90px; right: 70px; top: 190px;
    font-size: 11px; line-height: 1.55; text-align: justify; color: var(--ink);
  }
  .letter-body p { margin-bottom: 13px; }
  .sign-off {
    position: absolute; right: 70px; top: 520px; text-align: right;
    font-size: 11px;
  }
  .signature-row { display: flex; align-items: flex-end; gap: 14px; margin-top: 6px; }
  .signature {
    width: 110px; height: 44px;
    background: linear-gradient(90deg, rgba(60,80,170,0.05), rgba(60,80,170,0.22), rgba(60,80,170,0.05));
    border-radius: 4px;
  }
  .signer { font-size: 12px; color: #222; padding-bottom: 4px; }
  .attorney-roster {
    position: absolute; right: 70px; top: 650px;
    padding-right: 12px; border-right: 1px solid var(--rule);
    text-align: right; font-size: 9.5px; line-height: 1.45; color: var(--ink-soft);
  }
  .attorney-name { color: var(--ink); letter-spacing: 0.5px; }
  .attorney + .attorney { margin-top: 6px; }
  .contact-footer {
    position: absolute; left: 90px; bottom: 60px;
    display: flex; align-items: stretch; gap: 12px;
    font-size: 10.5px; line-height: 1.4; color: var(--brand-blue);
  }
  .contact-divider { width: 1px; background: var(--brand-blue); }
</style>
</head>
<body>
  <main class="letterhead">
    <header class="masthead">Pell &amp; Varnum, Attorneys-At-Law, LLP.</header>

    <div class="star-watermark" role="img" aria-label="Faint Texas star watermark"></div>

    <section class="letter-body">
      <p>Lorem ipsum dolor sit amet, consectetur adipiscing elit, sed do eiusmod tempor incididunt ut labore et dolore magna aliqua. Ut enim ad minim veniam, quis nostrud exercitation ullamco laboris nisi ut aliquip ex ea commodo consequat. Duis aute irure dolor in reprehenderit in voluptate velit esse cillum dolore eu fugiat nulla pariatur.</p>
      <p>Sed do eiusmod tempor incididunt ut labore et dolore magna aliqua, quis nostrud exercitation ullamco laboris nisi ut aliquip ex ea commodo. Excepteur sint occaecat cupidatat non proident, sunt in culpa qui officia deserunt mollit anim id est laborum.</p>
      <p>Ut enim ad minim veniam, quis nostrud exercitation ullamco laboris nisi ut aliquip ex ea commodo consequat. Duis aute irure dolor in reprehenderit in voluptate velit esse cillum dolore eu fugiat nulla pariatur.</p>
      <p>Sed do eiusmod tempor incididunt ut labore et dolore magna aliqua, quis nostrud exercitation ullamco laboris nisi ut aliquip ex ea commodo. Excepteur sint occaecat cupidatat non proident, sunt in culpa qui officia deserunt mollit anim id est laborum.</p>
    </section>

    <div class="sign-off">
      <div>Yours Sincerely,</div>
      <div class="signature-row">
        <div class="signature" role="img" aria-label="Handwritten signature"></div>
        <div class="signer">Nora Ellis</div>
      </div>
    </div>

    <aside class="attorney-roster">
      <div class="attorney">
        <div class="attorney-name">DANIEL PELL</div>
        <div>Managing Partner</div>
        <div>- Licensed in the State of Texas</div>
        <div>- U.S. District Court</div>
        <div>(Northern District of Texas)</div>
        <div>- United States Supreme Court</div>
      </div>
      <div class="attorney">
        <div class="attorney-name">LAURA JEAN VARNUM</div>
        <div>- Licensed in the State of Texas</div>
      </div>
    </aside>

    <footer class="contact-footer">
      <div class="contact-address">
        <div>2140 E. Rosedale St.</div>
        <div>Fort Worth, TX 76105</div>
      </div>
      <div class="contact-divider"></div>
      <div class="contact-lines">
        <div>Phone: (817) 555-0142</div>
        <div>Fax: (817) 555-0187</div>
      </div>
    </footer>
  </main>
</body>
</html>
```